Global Beard Oil Review Business needs a refresh

topwhiskertonic.net is a global business who's mission is to curate all available beard oils from around the world, review and grade them and present this curated collection to the user of the website.

The scope of this job includes the web site design and the design of a suitable logo to be used in the site header.

The existing site can be seen on http://topwhiskertonic.net, however this is a mock-up only the style and logo should NOT be used. This is to give you an idea of the concept of the site only.

This job is for PSD design only.

See attached design brief for detailed design requirements.
Updates

Project Deadline Extended
Reason: Extending deadline by 5 days to allow for final submissions

Target Market(s)

Men's grooming / retail

Industry/Entity Type

Retail

Number of Pages Required

2 page

Font styles to use
Sans Serif

Requirements
Must have
• 1) Comparison Table
• 2) Side Bar
• 3) Header area
• 4) Photo of Delvin Marsk (attached - can be circular or "cut-out")
• 5) Cool beard-oriented custom design background (e.g., stylistic black/brown on brown/orange beard background. I envision this beard background "drawing" rather than photo based)
• (see attached design requirements for details)
Nice to have
• Signature style writing at top with name "Delvin Marsk"
Should not have
• Do NOT use the look & feel or logo from the existing site.

```html
<!DOCTYPE html>
<html lang="en">
<head>
<meta charset="utf-8">
<title>Top Whisker Tonic</title>
<link href="https://fonts.googleapis.com/css2?family=Raleway:wght@400;500;600&family=Lato:wght@400;700&family=Roboto+Condensed:wght@400;700&family=Parisienne&display=swap" rel="stylesheet">
<style>
:root{
  --teal:#3db6b5;
  --orange:#f7922b;
  --ink:#262c33;
  --ink-soft:#2e353d;
  --text:#333;
  --table-bg:#e8f6f6;
  --blog-bg:#fdf1e3;
  --row-a:#d5e6e5;
  --row-b:#e3efee;
}
*{box-sizing:border-box;margin:0;padding:0}
html,body{width:716px;height:1200px;overflow:hidden;background:#fff}
body{position:relative;font-family:'Lato',sans-serif;color:var(--text)}
.abs{position:absolute}

/* header */
.site-header{left:0;top:0;width:716px;height:64px;background:var(--ink)}
.brand{left:118px;top:24px;font:700 14px/16px 'Lato',sans-serif;color:var(--teal);display:flex;align-items:center;gap:6px;white-space:nowrap}
.brand-dot{width:10px;height:10px;border-radius:50%;background:var(--orange)}
.main-nav{top:24px;left:0;width:716px;height:19px;font:400 9.5px 'Roboto Condensed',sans-serif}
.main-nav a{position:absolute;top:0;color:#fff;text-decoration:none;height:19px;line-height:17px;padding:0 8px;border:1px solid transparent;border-radius:3px;white-space:nowrap}
.main-nav a.active{border-color:var(--teal);color:var(--teal)}

/* hero */
.hero{left:0;top:64px;width:716px;height:246px;background:linear-gradient(180deg,#e9e7e3 0%,#dcd8d2 55%,#c9b8a2 78%,#d8cbbb 100%)}
.hero-bottles{left:400px;top:74px;width:300px;height:230px;background:radial-gradient(ellipse at 82% 55%,#5b2f1a 0,#6e3b1f 18%,rgba(110,59,31,0) 38%),radial-gradient(ellipse at 40% 50%,rgba(120,80,50,.45) 0,rgba(120,80,50,0) 35%)}
.hero-title{left:118px;top:133px;font:500 22.5px/23px 'Raleway',sans-serif;color:#333}
.hero-title .o{color:var(--orange);font-weight:600}
.hero-title .t{color:var(--teal);font-weight:600}
.btn-outline-dark{left:118px;top:217px;width:55px;height:19px;border:1.5px solid #333;border-radius:3px;font:400 8.5px/16px 'Roboto Condensed',sans-serif;text-align:center;color:#333}
.slider-dots{left:343px;top:289px;display:flex;gap:6px}
.slider-dots span{width:7px;height:7px;border-radius:50%;background:#fff}
.slider-dots span.on{background:var(--ink)}

/* about */
.about-band{left:0;top:310px;width:716px;height:221px;background:#fbfbfb}
.about-title{left:119px;top:330px;width:306px;font:400 18px/22px 'Raleway',sans-serif;color:var(--teal);border-bottom:1px solid #ccc;padding-bottom:1px}
.about-title span{color:var(--orange)}
.about-copy{left:119px;top:363px;width:308px;font:400 6.9px/9.2px 'Lato',sans-serif;color:#444}
.about-copy p{margin-bottom:6px}
.btn-outline-teal{left:119px;top:474px;width:58px;height:18px;border:1.5px solid var(--teal);border-radius:3px;font:400 8px/15px 'Roboto Condensed',sans-serif;text-align:center;color:var(--teal);background:#fff}
.portrait-frame{left:451px;top:334px;width:146px;height:144px;border:1px solid #ccc;background:#fff;padding:4px}
.portrait{width:100%;height:100%;background:linear-gradient(135deg,#bcbcbc,#5a5a5a 60%,#2e2e2e)}
.signature{left:498px;top:485px;font:400 16px 'Parisienne',cursive;color:#222}

/* reviews table */
.reviews-band{left:0;top:531px;width:716px;height:361px;background:var(--table-bg)}
.reviews-title{left:0;top:557px;width:716px;text-align:center;font:400 18px/22px 'Raleway',sans-serif;color:#222}
.reviews-intro{left:125px;top:584px;width:466px;text-align:center;font:400 6.6px/8.6px 'Lato',sans-serif;color:#333}
.review-table{left:118px;top:623px;width:479px;border-collapse:collapse;font:400 7.4px 'Lato',sans-serif;color:#333;table-layout:fixed}
.review-table th{height:23px;background:var(--ink-soft);color:var(--teal);font:400 7.6px 'Roboto Condensed',sans-serif;border-right:1px solid #4a525b;text-align:center}
.review-table th.score{background:var(--teal);color:#fff;border-right-color:#6cc9c8}
.review-table th:first-child,.review-table td:first-child{text-align:left;padding-left:5px}
.review-table td{height:49px;text-align:center;border-right:1px solid #c6dad9;font-weight:400}
.review-table tr:nth-child(odd) td{background:var(--row-a)}
.review-table tr:nth-child(even) td{background:var(--row-b)}
.thumb{display:inline-block;width:28px;height:35px;background:linear-gradient(90deg,#efe6cf 0,#efe6cf 25%,#1f1f1f 35%,#2b2b2b 65%,#efe6cf 75%);border:1px solid #d8ccb0;vertical-align:middle}
.buy{display:inline-block;width:45px;height:19px;line-height:19px;background:var(--orange);color:#fff;border-radius:2px;font:400 8px/19px 'Roboto Condensed',sans-serif;box-shadow:0 2px 0 #c66e17}
.more-tab{left:345px;top:879px;width:27px;height:14px;border-radius:14px 14px 0 0;background:#4a5562}

/* blog */
.blog-band{left:0;top:892px;width:716px;height:218px;background:var(--blog-bg)}
.blog-title{left:0;top:918px;width:716px;text-align:center;font:400 18px/22px 'Raleway',sans-serif;color:var(--teal)}
.blog-rule{left:200px;top:942px;width:312px;height:1px;background:#cfc6ba}
.blog-rule::after{content:"";position:absolute;left:143px;top:-1px;width:28px;height:2px;background:#666}
.post{top:975px;width:231px;height:101px;background:#fff;display:flex}
.post-photo{width:102px;height:101px;flex:none}
.post-body{padding:17px 9px 0 11px;width:129px}
.post-body h3{font:700 7.8px/10.5px 'Lato',sans-serif;color:#222;padding-bottom:5px;border-bottom:1px solid #ccc;margin-bottom:5px}
.post-body p{font:400 6.6px/8.8px 'Lato',sans-serif;color:#444}
.post-body p b{color:var(--orange);font-weight:400}
.date{top:959px;width:31px;height:28px;background:var(--teal);color:#fff;text-align:center;font:400 8px 'Lato',sans-serif;line-height:9px;padding-top:2px}
.date strong{display:block;font:700 13px/14px 'Lato',sans-serif}
.arrow{top:1012px;width:13px;height:25px;background:var(--ink)}
.arrow.prev{left:97px;border-radius:13px 0 0 13px}
.arrow.next{left:606px;border-radius:0 13px 13px 0}

/* footer */
.footer-nav{left:0;top:1110px;width:716px;height:31px;background:var(--orange);text-align:center;font:400 7.4px/31px 'Lato',sans-serif;color:#fff}
.footer-nav span{margin:0 3px}
.site-footer{left:0;top:1141px;width:716px;height:59px;background:var(--ink)}
.contact-icons{left:134px;top:1155px;display:flex;gap:3px}
.contact-icons span{width:18px;height:18px;border-radius:50%;display:flex;align-items:center;justify-content:center}
.footer-brand{left:181px;top:1159px;font:700 11px 'Lato',sans-serif;color:var(--teal)}
.copyright{left:135px;top:1182px;font:400 6px 'Lato',sans-serif;color:#ddd}
.follow{left:470px;top:1160px;font:700 11px 'Lato',sans-serif;color:#fff}
.social{left:530px;top:1160px;display:flex;gap:4px}
.social span{width:14px;height:14px;border-radius:50%;background:#fff}
</style>
</head>
<body>

<header class="site-header abs"></header>
<div class="brand abs"><span class="brand-dot"></span>Top Whisker Tonic</div>
<nav class="main-nav abs">
  <a class="active" style="left:296px">Home</a><a style="left:341px">About Me</a><a style="left:399px">Our Charter</a><a style="left:463px">Beard Oil Methodology</a><a style="left:568px">BLog</a>
</nav>

<section class="hero abs" role="img" aria-label="Amber dropper bottles of beard oil on a wooden table"></section>
<div class="hero-bottles abs" role="img" aria-label="Beard oil bottles"></div>
<h1 class="hero-title abs"><span class="o">Beard Oil</span> with <span class="t">Argan Kukui</span><br><span class="t">Babbasu Citrus</span> Mint<br>Essential Oils</h1>
<div class="btn-outline-dark abs">Read More</div>
<div class="slider-dots abs"><span class="on"></span><span></span><span></span></div>

<section class="about-band abs"></section>
<h2 class="about-title abs">About <span>Delvin Marsk</span></h2>
<div class="about-copy abs">
  <p>Sed ut perspiciatis unde omnis iste natus error sit voluptatem accusantium doloremque laudantium, totam rem aperiam, eaque ipsa quae ab illo inventore veritatis et quasi architecto beatae vitae dicta sunt explicabo. Nemo enim ipsam voluptatem quia voluptas sit aspernatur aut odit aut fugit, sed quia consequuntur magni dolores eos qui ratione voluptatem sequi nesciunt. Neque porro quisquam est, qui dolorem ipsum quia dolor sit amet, consectetur, adipisci velit, sed quia non numquam eius modi tempora incidunt ut labore et dolore magnam aliquam quaerat voluptatem.</p>
  <p>Sed ut perspiciatis unde omnis iste natus error sit voluptatem accusantium doloremque laudantium, totam rem aperiam, eaque ipsa quae ab illo inventore veritatis et quasi architecto beatae vitae dicta sunt explicabo.</p>
</div>
<div class="btn-outline-teal abs">Read More</div>
<div class="portrait-frame abs"><div class="portrait" role="img" aria-label="Black and white photo of Delvin Marsk"></div></div>
<div class="signature abs">- Delvin Marsk</div>

<section class="reviews-band abs"></section>
<h2 class="reviews-title abs">The World’s #1 Beard Oil Authority</h2>
<p class="reviews-intro abs">Here is the master list of beard oils reviewed to date. You can link directly to the corresponding review by clicking on the name of the beard oil. In accordance with our charter, we are actively working to locate and review every single beard oil available on the planet Earth.</p>
<table class="review-table abs">
  <colgroup><col style="width:74px"><col style="width:54px"><col style="width:41px"><col style="width:35px"><col style="width:46px"><col style="width:38px"><col style="width:34px"><col style="width:34px"><col style="width:34px"><col style="width:35px"><col style="width:54px"></colgroup>
  <thead><tr><th>Supplier</th><th>Name</th><th>Photo</th><th>Origin</th><th>Base Oil</th><th>Scent</th><th class="score">Aroma</th><th class="score">Affect</th><th class="score">Value</th><th class="score">Overall</th><th class="score">links</th></tr></thead>
  <tbody>
    <tr><td>Grizzle &amp; Pine</td><td>Timberline</td><td><span class="thumb" role="img" aria-label="Beard oil bottle"></span></td><td>USA</td><td>Lpsum</td><td>Lpsum</td><td>7</td><td>5</td><td>1</td><td>3</td><td><span class="buy">Buy Now</span></td></tr>
    <tr><td>Grizzle &amp; Pine</td><td>Timberline</td><td><span class="thumb" role="img" aria-label="Beard oil bottle"></span></td><td>USA</td><td>Lpsum</td><td>Lpsum</td><td>7</td><td>5</td><td>1</td><td>3</td><td><span class="buy">Buy Now</span></td></tr>
    <tr><td>Grizzle &amp; Pine</td><td>Timberline</td><td><span class="thumb" role="img" aria-label="Beard oil bottle"></span></td><td>USA</td><td>Lpsum</td><td>Lpsum</td><td>7</td><td>5</td><td>1</td><td>3</td><td><span class="buy">Buy Now</span></td></tr>
    <tr><td>Grizzle &amp; Pine</td><td>Timberline</td><td><span class="thumb" role="img" aria-label="Beard oil bottle"></span></td><td>USA</td><td>Lpsum</td><td>Lpsum</td><td>7</td><td>5</td><td>1</td><td>3</td><td><span class="buy">Buy Now</span></td></tr>
  </tbody>
</table>
<div class="more-tab abs"><svg width="27" height="14" viewBox="0 0 27 14"><path d="M13.5 4v7M10 7.5h7" stroke="#fff" stroke-width="2"/></svg></div>

<section class="blog-band abs"></section>
<h2 class="blog-title abs">Latest Blog</h2>
<div class="blog-rule abs"></div>
<div class="arrow prev abs"><svg width="13" height="25"><path d="M9 8l-5 4.5 5 4.5z" fill="#fff"/></svg></div>
<article class="post abs" style="left:118px">
  <div class="post-photo" role="img" aria-label="Dropper of beard oil against green foliage" style="background:linear-gradient(160deg,#6f8a3a,#2f4a1e 60%,#1d2a12)"></div>
  <div class="post-body"><h3>Eaque ipsa quae ab illo inventore veritatis et quasi .</h3><p>Sed ut perspiciatis unde omnis iste natus error sit voluptatem accusan tium doloremque laudantium, totam rem aperiam, <b>+</b></p></div>
</article>
<div class="date abs" style="left:309px"><strong>12</strong>Feb</div>
<article class="post abs" style="left:367px">
  <div class="post-photo" role="img" aria-label="Burlap pouch of beard care product on a table" style="background:linear-gradient(180deg,#b8ab92,#8a7a5c 60%,#6d5f47)"></div>
  <div class="post-body"><h3>Eaque ipsa quae ab illo inventore veritatis et quasi .</h3><p>Sed ut perspiciatis unde omnis iste natus error sit voluptatem accusan tium doloremque laudantium, totam rem aperiam, <b>+</b></p></div>
</article>
<div class="date abs" style="left:558px"><strong>10</strong>Feb</div>
<div class="arrow next abs"><svg width="13" height="25"><path d="M4 8l5 4.5-5 4.5z" fill="#fff"/></svg></div>

<nav class="footer-nav abs">Home <span>|</span> About Me <span>|</span> Our Charter <span>|</span> Beard Oil Methodology <span>|</span> Blog</nav>
<footer class="site-footer abs"></footer>
<div class="contact-icons abs">
  <span style="background:var(--orange)"><svg width="8" height="11"><rect x="1" y="0.5" width="6" height="10" rx="1" fill="none" stroke="#fff"/></svg></span>
  <span style="background:#fff"><svg width="10" height="7"><rect x="0.5" y="0.5" width="9" height="6" fill="none" stroke="#262c33"/><path d="M.5.5l4.5 3.5L9.5.5" fill="none" stroke="#262c33"/></svg></span>
</div>
<div class="footer-brand abs">Top Whisker Tonic</div>
<div class="copyright abs">Copyright © 2016 Top Whisker Tonic. All rights reserved.</div>
<div class="follow abs">Follow Us</div>
<div class="social abs"><span></span><span></span><span></span><span></span></div>

</body>
</html>
```